Business card for Luxury Portable Restroom Trailer company

We are a Luxury Portable Restroom Trailer Company Called FALCRIDGE HIRES. Based in Orange County California. We provide portable restroom trailers for events, such as, Weddings, Concerts, Charity events, Sporting events, Tournaments, Corporate events, ect. We rent and Sell the Luxury restrooms. Our colors are white, grey, and Orange. As you will see in the logo we uploaded.
There are 2 people in the company so the names and titles will change for the 3 people but card will remain the same. Here is the information for each Person: Dwight Penner CFO 555 318-0476
next Person: Leon Marchetti VP 555 318-0476
Next Person: Owen Marchetti CEO 555 318-0476
Information to include on the card: Luxury Restroom Trailers Rental and Sales. Weddings, Concerts, Charity, Sporting and Corp. Events.

```html
<!DOCTYPE html>
<html lang="en">
<head>
<meta charset="utf-8">
<title>Falcridge Hires – Business Card</title>
<link href="https://fonts.googleapis.com/css2?family=Michroma&display=swap" rel="stylesheet">
<style>
  :root {
    --backdrop: #1c1c1c;
    --card-white: #ffffff;
    --card-grey: #4a4a4c;
    --card-grey-light: #5a5a5d;
    --brand-orange: #f26a21;
    --text-grey: #58595b;
    --emboss: #3a3a3c;
  }
  * { margin: 0; padding: 0; box-sizing: border-box; }
  html, body {
    width: 1200px;
    height: 876px;
    overflow: hidden;
    background: var(--backdrop);
    font-family: "Michroma", "Helvetica Neue", Arial, sans-serif;
  }
  .canvas {
    position: relative;
    width: 1200px;
    height: 876px;
    display: flex;
    align-items: center;
    justify-content: center;
    gap: 48px;
  }
  .card {
    width: 500px;
    height: 286px;
    position: relative;
  }
  /* Front */
  .card--front {
    background: var(--card-white);
    padding: 28px 34px;
  }
  .brand {
    display: flex;
    align-items: center;
    justify-content: center;
    gap: 10px;
    margin-top: 6px;
  }
  .brand__square {
    width: 18px;
    height: 18px;
    background: var(--brand-orange);
  }
  .brand__name {
    color: var(--brand-orange);
    font-size: 22px;
    letter-spacing: 1px;
  }
  .person {
    text-align: center;
    margin-top: 26px;
  }
  .person__name {
    font-size: 19px;
    letter-spacing: 0.5px;
    color: var(--text-grey);
  }
  .person__first { color: var(--brand-orange); }
  .person__title {
    font-size: 12px;
    color: var(--text-grey);
    margin-top: 4px;
  }
  .person__phone {
    display: inline-flex;
    align-items: center;
    gap: 6px;
    font-size: 13px;
    color: var(--text-grey);
    margin-top: 10px;
  }
  .person__phone svg { width: 12px; height: 12px; }
  .services {
    position: absolute;
    left: 34px;
    bottom: 24px;
    font-size: 9.5px;
    line-height: 1.8;
    color: var(--text-grey);
  }
  .services .sep { color: var(--brand-orange); }
  /* Back */
  .card--back {
    background: linear-gradient(135deg, var(--card-grey-light), var(--card-grey));
    display: flex;
    align-items: center;
    justify-content: center;
    gap: 14px;
  }
  .back-mark {
    width: 40px;
    height: 40px;
    border: 3px solid var(--emboss);
    border-radius: 50%;
  }
  .back-name {
    color: var(--emboss);
    font-size: 20px;
    letter-spacing: 1px;
  }
</style>
</head>
<body>
<main class="canvas">
  <section class="card card--front">
    <div class="brand">
      <span class="brand__square"></span>
      <span class="brand__name">FALCRIDGE HIRES</span>
    </div>
    <div class="person">
      <p class="person__name"><span class="person__first">DWIGHT</span> PENNER</p>
      <p class="person__title">CFO</p>
      <p class="person__phone">
        <svg viewBox="0 0 24 24" aria-hidden="true"><path fill="#f26a21" d="M6.6 10.8a15.1 15.1 0 0 0 6.6 6.6l2.2-2.2c.3-.3.7-.4 1-.2 1.1.4 2.3.6 3.6.6.6 0 1 .4 1 1V20c0 .6-.4 1-1 1A17 17 0 0 1 3 4c0-.6.4-1 1-1h3.5c.6 0 1 .4 1 1 0 1.3.2 2.5.6 3.6.1.3 0 .7-.2 1l-2.3 2.2z"/></svg>
        555.318.0476
      </p>
    </div>
    <div class="services">
      <p>Luxury Restroom Trailers Rental and Sales <span class="sep">|</span> Weddings</p>
      <p>Concerts <span class="sep">|</span> Charity <span class="sep">|</span> Sporting <span class="sep">|</span> Corp. Events.</p>
    </div>
  </section>
  <section class="card card--back">
    <span class="back-mark"></span>
    <span class="back-name">FALCRIDGE HIRES</span>
  </section>
</main>
</body>
</html>
```